Brookvane Consulting Business Card Design

Business Card Design for Brookvane Consulting. Brookvane Consulting is a boutique consultancy based in Atlanta, GA., that specializes in marketing strategy, organization planning, and leadership development. We provide solutions for small businesses and startups as well as Vantage 300 companies.

http://brookvaneconsulting.com/

Target Market(s)

We provide solutions for small businesses and startups as well as Vantage 300 companies.

Industry/Entity Type

Consulting

Contact Information for Business Card

Two sided business card with priority on contact information, logo, tag line (Inspiration to Dream More, Do More, Become More)

Colors

Designer to choose colors to be used in the design.

Requirements
Must have
• contact information, logo, tag line (Inspiration to Dream More, Do More, Become More)
• Simple no over communication.
Nice to have
• I would like to see different placements of logo and creative use of both sides of the card
Should not have
• Do not put too much information on the card.

```html
<!DOCTYPE html>
<html lang="en">
<head>
<meta charset="utf-8">
<title>Brookvane Consulting Business Card</title>
<link rel="stylesheet" href="https://fonts.googleapis.com/css2?family=Roboto:wght@400;500&family=Roboto+Condensed:wght@500&display=swap">
<style>
  :root {
    --backdrop: #e6e2dd;
    --card-dark: #1f2022;
    --card-front: #242527;
    --card-stack: #1a1b1d;
    --ink-white: #ffffff;
    --ink-soft: #e4e4e4;
    --ink-grey: #b8b8b8;
    --rule: #8a8a8a;
    --band: #ffffff;
    --band-ink: #222325;
  }
  html, body {
    margin: 0;
    padding: 0;
    width: 1200px;
    height: 960px;
    overflow: hidden;
    background: var(--backdrop);
    font-family: "Roboto", Arial, sans-serif;
  }
  .canvas {
    position: relative;
    width: 1200px;
    height: 960px;
  }
  .card {
    position: absolute;
    left: 320px;
    width: 600px;
    box-shadow: 0 4px 10px rgba(0,0,0,0.35);
  }
  .card-front-stack {
    top: 92px;
    height: 370px;
    background: var(--card-stack);
    left: 312px;
    width: 618px;
  }
  .card-front {
    top: 100px;
    height: 340px;
    background: var(--card-front);
  }
  .card-front .pattern {
    position: absolute;
    inset: 0;
    background: linear-gradient(180deg, #27282a, #202123);
  }
  .wordmark {
    position: absolute;
    color: var(--ink-white);
    font-family: "Roboto", Arial, sans-serif;
    font-weight: 500;
    font-size: 34px;
    letter-spacing: 0.5px;
    white-space: nowrap;
  }
  .card-front .wordmark {
    left: 0;
    right: 0;
    top: 145px;
    text-align: center;
  }
  .tagline {
    position: absolute;
    left: 0;
    right: 0;
    top: 288px;
    text-align: center;
    color: var(--ink-soft);
    font-size: 14px;
  }
  .card-back {
    top: 493px;
    height: 342px;
    background: var(--card-dark);
    overflow: hidden;
  }
  .card-back .wordmark {
    right: 35px;
    top: 70px;
  }
  .holder-name {
    position: absolute;
    left: 29px;
    top: 195px;
    font-family: "Roboto Condensed", Arial, sans-serif;
    font-weight: 500;
    font-size: 21px;
    color: var(--ink-grey);
    letter-spacing: 0.3px;
  }
  .holder-title {
    position: absolute;
    left: 29px;
    top: 221px;
    font-size: 15px;
    font-weight: 500;
    color: var(--ink-white);
  }
  .divider {
    position: absolute;
    left: 29px;
    top: 250px;
    width: 542px;
    height: 1px;
    background: var(--rule);
  }
  .contact-line {
    position: absolute;
    left: 29px;
    display: flex;
    align-items: center;
    gap: 8px;
    font-size: 14px;
    color: var(--ink-soft);
  }
  .contact-phone { top: 261px; }
  .contact-email { top: 281px; }
  .contact-line svg { width: 13px; height: 13px; fill: #a8a8a8; }
  .footer-band {
    position: absolute;
    left: 0;
    bottom: 0;
    width: 600px;
    height: 30px;
  }
  .website {
    position: absolute;
    right: 15px;
    bottom: 4px;
    font-size: 13px;
    font-weight: 500;
    letter-spacing: 1.6px;
    color: var(--band-ink);
  }
</style>
</head>
<body>
<main class="canvas">
  <div class="card card-front-stack" aria-hidden="true"></div>

  <section class="card card-front" aria-label="Card front">
    <div class="pattern" role="img" aria-label="Subtle dark grid texture pattern"></div>
    <div class="wordmark">Brookvane Consulting</div>
    <p class="tagline" style="margin:0">Inspiration to Dream More, Do More, Become More</p>
  </section>

  <section class="card card-back" aria-label="Card back">
    <div class="wordmark">Brookvane Consulting</div>
    <div class="holder-name">DARIUS WHITFIELD</div>
    <div class="holder-title">Founder/Managing Director</div>
    <div class="divider"></div>
    <div class="contact-line contact-phone">
      <svg viewBox="0 0 24 24" aria-hidden="true"><path d="M6.6 10.8a15.1 15.1 0 0 0 6.6 6.6l2.2-2.2c.3-.3.7-.4 1-.2 1.1.4 2.3.6 3.6.6.6 0 1 .4 1 1V20c0 .6-.4 1-1 1A17 17 0 0 1 3 4c0-.6.4-1 1-1h3.5c.6 0 1 .4 1 1 0 1.3.2 2.5.6 3.6.1.3 0 .7-.2 1z"/></svg>
      <span>424-555-0198</span>
    </div>
    <div class="contact-line contact-email">
      <svg viewBox="0 0 24 24" aria-hidden="true"><path d="M2 5h20v14H2z M2 5l10 7 10-7" stroke="#1f2022" stroke-width="1.5"/></svg>
      <span>darius@brookvaneconsulting.com</span>
    </div>
    <svg class="footer-band" viewBox="0 0 600 30" aria-hidden="true">
      <polygon points="0,18 310,18 300,30 0,30" fill="var(--band)"/>
      <polygon points="304,30 316,18 320,18 308,30" fill="var(--band)"/>
      <polygon points="330,30 342,6 600,6 600,30" fill="var(--band)"/>
    </svg>
    <div class="website">www.brookvaneconsulting.com</div>
  </section>
</main>
</body>
</html>
```